Halvik - consultancy website

I need a new design for my webpage/presence [to be functioning with Wordpress - I have a programmer to set it up but not the design idea].
My company is Halvik - a consultancy firm focused on growth management for Swedish SME's primarily;. We call it Leadership toolkit for firms on the rise, kind of a doctor helping small become big. Contentwise, its a simple frontpage + 3-4 subpages with content re company/myself/focus etc. The new site should communicate a fresh, trustworthy take yet simple and functional on all devices [i.e. think UI compatible for mobile/tablet]. Current building parts/form elements are
a) existing logo and text elements
b) existing pictures
c) the yellowish color
colours and new ideas on pictures/positioning are welcome. I prefer a 'full width page' solution with centralised text elements but that's all up to you to suggest. Current site is a quickfix made by myself - now I'm moving it to a new platform so want to take the opportunity to make it
Nothing superspecial as it is a 2-man show; on the other hand I still want to have a modern & fresh reflection of my brand in digital environments. Help me out!
www.halvik-demo.se
Best
Lina Bergqvist

```html
<!DOCTYPE html>
<html lang="en">
<head>
<meta charset="utf-8">
<title>Halvik – Who we are</title>
<link rel="stylesheet" href="https://fonts.googleapis.com/css2?family=Noticia+Text:ital,wght@0,400;0,700;1,400&display=swap">
<style>
  :root {
    --ink: #333333;
    --body-text: #4a4a4a;
    --accent: #e8920f;
    --orange: #f0a43c;
    --yellow: #fcd21c;
    --footer: #3f3f3f;
    --white: #ffffff;
    --header-top: #ffffff;
    --header-bottom: #f0f0f0;
    --serif: "Noticia Text", Georgia, serif;
    --sans: Helvetica, Arial, sans-serif;
  }
  * { box-sizing: border-box; margin: 0; padding: 0; }
  html, body { width: 1200px; height: 922px; overflow: hidden; }
  body {
    position: relative;
    background: var(--white);
    font-family: var(--serif);
    color: var(--ink);
  }

  .site-header {
    position: absolute; left: 0; top: 0; width: 1200px; height: 103px;
    background: linear-gradient(var(--header-top), var(--header-bottom));
  }
  .brand {
    position: absolute; left: 74px; top: 16px;
    font-family: var(--serif); font-size: 60px; font-weight: 400;
    color: var(--ink); letter-spacing: -0.5px; line-height: 1;
  }
  .main-nav {
    position: absolute; right: 75px; top: 54px;
    display: flex; gap: 0;
  }
  .main-nav a {
    display: block; font-size: 17px; color: var(--ink); text-decoration: none;
    padding: 0 7px 6px; margin-left: 35px;
  }
  .main-nav a.is-active { color: var(--accent); border-bottom: 2px solid var(--accent); }

  .tiles {
    position: absolute; left: 75px; top: 148px;
    display: flex; gap: 17.5px;
  }
  .tile { width: 339px; height: 321px; }
  .tile-photo-desk { background: linear-gradient(135deg, #6f655b 0%, #8a7e70 40%, #c54a7d 75%, #5e564d 100%); }
  .tile-photo-city { background: linear-gradient(180deg, #dfe6ea 0%, #c9d2cf 40%, #8a7a55 62%, #3f3a2c 100%); }
  .tile-quote {
    background: var(--orange); color: var(--white);
    padding: 30px 21px 0 19px; text-align: right;
  }
  .tile-quote blockquote {
    font-style: italic; font-size: 16.5px; line-height: 22px; text-align: justify;
    text-align-last: right;
  }
  .tile-quote .cite { margin-top: 28px; font-size: 16.5px; line-height: 22px; }
  .tile-quote .cite span { display: block; font-style: italic; }

  .portrait {
    position: absolute; left: 75px; top: 506px; width: 193px; height: 326px;
    background: linear-gradient(180deg, #f4f4f4 0%, #d6d6d6 35%, #2b2b2b 60%, #1f1f1f 100%);
  }
  .intro { position: absolute; left: 304px; top: 546px; width: 422px; }
  .intro h1 {
    font-size: 24px; font-weight: 400; letter-spacing: 0.5px; color: var(--ink);
    margin-bottom: 20px;
  }
  .intro p {
    font-size: 15px; line-height: 22px; color: var(--body-text);
    text-align: justify; letter-spacing: 0.3px; margin-bottom: 22px;
  }
  .read-more {
    display: inline-block; margin-top: -10px;
    font-size: 15px; color: var(--accent); text-decoration: none; letter-spacing: 0.8px;
  }

  .signup {
    position: absolute; left: 794px; top: 599px; width: 332px; height: 148px;
    background: var(--yellow);
  }
  .signup-badge { position: absolute; left: 14px; top: 14px; }
  .signup-text {
    position: absolute; left: 113px; top: 30px;
    font-size: 15.5px; line-height: 22px; color: var(--ink);
  }
  .signup-field {
    position: absolute; left: 113px; top: 86px; width: 197px; height: 37px; display: flex;
  }
  .signup-field input {
    flex: 1; border: 0; outline: 0; background: var(--white);
    font-family: var(--sans); font-size: 13px; color: #888; padding: 0 16px;
  }
  .signup-field input::placeholder { color: #8c8c8c; }
  .signup-field button {
    width: 38px; border: 0; background: var(--orange);
    display: flex; align-items: center; justify-content: center;
  }

  .site-footer {
    position: absolute; left: 0; top: 832px; width: 1200px; height: 90px;
    background: var(--footer); color: var(--white);
  }
  .footer-info { position: absolute; left: 76px; top: 24px; font-size: 14.5px; line-height: 28px; }
  .footer-info .contact span + span { margin-left: 27px; }
  .social { position: absolute; right: 75px; top: 33px; display: flex; gap: 13px; }
  .social a {
    display: block; width: 32px; height: 32px; border-radius: 3px;
    background: #6b6b6b; border: 1px solid #808080;
  }
</style>
</head>
<body>
  <header class="site-header">
    <div class="brand">Halvik.</div>
    <nav class="main-nav">
      <a href="#">Home</a>
      <a href="#">What we do</a>
      <a href="#" class="is-active">Who we are</a>
      <a href="#">Why us</a>
    </nav>
  </header>

  <section class="tiles">
    <div class="tile tile-photo-desk" role="img" aria-label="Desk with camera, glasses, notebook and pink phone cases"></div>
    <div class="tile tile-quote">
      <blockquote>"Important deliverables under Linas responsibility has involved not only the creation of many successful creative product strategies, but also constructing efficient process flows and forming organizational structures to meet with market developments."</blockquote>
      <p class="cite">Anders Holm,<span>former CEO of Norvik Group</span></p>
    </div>
    <div class="tile tile-photo-city" role="img" aria-label="City skyline with a bridge over a river"></div>
  </section>

  <div class="portrait" role="img" aria-label="Black and white portrait of the consultant with arms crossed"></div>

  <section class="intro">
    <h1>GROWTH&nbsp; ENABLER.</h1>
    <p>Independent consulting across several diciplines, supporting businesses influenced by a ’fast forward’ mindset and desire to optimize its operations.</p>
    <p>With a background in Marketing and Economics, I've spent the past 10 years in the exiting space where Telecom &amp; IT meets fashion industry.</p>
    <a class="read-more" href="#">READ MORE</a>
  </section>

  <aside class="signup">
    <svg class="signup-badge" width="84" height="86" viewBox="0 0 84 86" role="img" aria-label="Get in touch speech bubble badge">
      <ellipse cx="42" cy="82" rx="40" ry="2" fill="#d9b416"/>
      <path d="M42 4a35 35 0 1 1 -8 69l-6 8l-1 -10a35 35 0 0 1 15 -67z" fill="#3d3d3d"/>
    </svg>
    <p class="signup-text">Simply drop your Email<br>here...</p>
    <form class="signup-field">
      <input type="email" placeholder="Enter Email">
      <button type="submit" aria-label="Submit">
        <svg width="10" height="14" viewBox="0 0 10 14"><path d="M2 2l5 5l-5 5" fill="none" stroke="#fff" stroke-width="2.5"/></svg>
      </button>
    </form>
  </aside>

  <footer class="site-footer">
    <div class="footer-info">
      <p>Halvik © 2015 | Privacy Policy</p>
      <p class="contact"><span>T: +46 [0] 700 12 34 56</span><span>E: info@halvik-demo.se</span></p>
    </div>
    <nav class="social">
      <a href="#" aria-label="Social profile 1"></a>
      <a href="#" aria-label="Social profile 2"></a>
      <a href="#" aria-label="Social profile 3"></a>
      <a href="#" aria-label="Social profile 4"></a>
    </nav>
  </footer>
</body>
</html>
```